Brivane Management

We need a web design for a new consulting company, with clients all over the world. The company provides management consulting to the travel industry.

Logo files are attached.

Website must look very corporate and be responsive in design.

Management Consulting

```html
<!DOCTYPE html>
<html lang="en">
<head>
<meta charset="utf-8">
<title>Brivane Management</title>
<link href="https://fonts.googleapis.com/css2?family=Roboto:wght@400;500;700&family=Oswald:wght@400&family=Cinzel:wght@400&family=Open+Sans:wght@400;600&display=swap" rel="stylesheet">
<style>
:root{
  --navy:#0b1838;
  --blue-top:#3b8fdc;
  --blue-bottom:#0d58a6;
  --green:#5cb82a;
  --green-dark:#3f9a14;
  --text:#333;
  --muted:#555;
  --page:#e6e6e6;
  --panel:#f5f5f5;
  --footer:#1c1c1c;
  --footer-deep:#0f0f0f;
  --line:#d8d8d8;
}
*{box-sizing:border-box;margin:0;padding:0}
html,body{width:800px;height:1200px;overflow:hidden}
body{position:relative;background:var(--page);font-family:"Roboto",sans-serif;color:var(--text)}
.abs{position:absolute}
.topstrip{left:0;top:0;width:800px;height:5px;background:var(--navy)}
.header{left:0;top:5px;width:800px;height:65px;background:linear-gradient(#fff,#f1f1f1)}
.brand{left:90px;top:16px;display:flex;align-items:center;gap:10px}
.brand-dot{width:40px;height:40px;border-radius:50%;background:var(--blue-bottom)}
.brand-name{font-family:"Roboto",sans-serif;font-weight:700;font-size:25px;color:#1a2a5a;letter-spacing:.5px}
.help{left:603px;top:22px;display:flex;gap:8px;align-items:center}
.help-icon{width:25px;height:25px;border-radius:4px;background:#333;display:flex;align-items:center;justify-content:center}
.help small{display:block;font-size:8px;color:#777;letter-spacing:.5px}
.help strong{font-size:14px;color:#333;font-weight:500}
.nav{left:0;top:70px;width:800px;height:29px;background:linear-gradient(var(--blue-top),var(--blue-bottom));border-top:1px solid #6aaee8}
.nav a{position:absolute;top:0;height:29px;line-height:29px;font-family:"Cinzel",serif;font-size:12.5px;color:#fff;text-decoration:none;letter-spacing:.5px;text-align:center;border-right:1px solid rgba(255,255,255,.25)}
.nav a.active{background:linear-gradient(#7bcc3e,var(--green-dark))}
.search{left:577px;top:3px;width:134px;height:23px;background:#fff;border-radius:3px;overflow:hidden}
.search span{position:absolute;left:8px;top:5px;font-size:8px;color:#aaa}
.search i{position:absolute;right:0;top:0;width:25px;height:23px;background:#222;display:flex;align-items:center;justify-content:center}
.hero{left:0;top:99px;width:800px;height:255px;background:linear-gradient(90deg,#3f4f6a 0%,#6f8199 35%,#8b9db2 55%,#a3b2c3 100%)}
.hero-copy{right:98px;top:138px;width:250px;text-align:right}
.hero-copy h1{font-family:"Oswald",sans-serif;font-weight:400;font-size:18.5px;line-height:23px;color:#1c2638}
.hero-copy p{margin-top:9px;font-size:10.5px;line-height:15px;color:#2c3a50}
.learn{left:604px;top:257px;width:96px;height:24px;border-radius:12px;background:linear-gradient(#86d24a,var(--green-dark));color:#fff;font-size:11.5px;font-weight:700;text-align:center;line-height:24px}
.arrow{width:26px;height:26px;border-radius:50%;background:rgba(40,50,70,.55);display:flex;align-items:center;justify-content:center}
.panel{left:89px;top:354px;width:625px;height:599px;background:var(--panel);box-shadow:0 0 6px rgba(0,0,0,.15)}
.box{top:373px;width:187px;height:176px;background:#fff;border:1px solid #d6d6d6;border-radius:6px;overflow:hidden}
.box-head{height:34px;display:flex;align-items:center;gap:7px;padding-left:8px;background:linear-gradient(#fff,#eee);border-bottom:1px solid #e0e0e0;font-size:12.5px;font-weight:500;color:#222}
.box-head b{width:22px;height:22px;border-radius:50%;background:var(--blue-bottom);display:block}
.box-head em{font-style:normal;color:var(--green)}
.box-body{padding:6px 8px;font-size:8.5px;line-height:12.4px;color:#333}
.plus{position:absolute;right:0;bottom:0;width:28px;height:28px;background:linear-gradient(135deg,transparent 50%,#1568c2 50%)}
.plus::after{content:"+";position:absolute;right:3px;bottom:-1px;color:#fff;font-size:14px;font-weight:700}
.news{display:flex;gap:8px;margin-bottom:8px}
.date{width:21px;flex:none;text-align:center;font-size:7px;color:#fff}
.date span{display:block;background:#777;height:11px;line-height:11px}
.date span+span{background:#444}
.news h3{font-size:8.5px;font-weight:700;margin-bottom:2px}
.field{margin:0 6px 4px;height:22px;border:1px solid #ccc;font-size:8.5px;color:#666;padding:5px 5px}
.tab{left:327px;top:583px;width:140px;height:20px;background:linear-gradient(#fff,#e5e5e5);border:1px solid #ccc;border-top:none;clip-path:polygon(0 0,100% 0,88% 100%,12% 100%);text-align:center;font-size:12.5px;font-weight:500;line-height:20px;color:#333}
.tabline{left:89px;top:583px;width:625px;height:1px;background:#ccc}
.tab em{font-style:normal;color:var(--green)}
.service{width:290px;display:flex;gap:12px}
.service-icon{width:57px;height:48px;flex:none;background:linear-gradient(#f8f8f8,#dcdcdc);border:1px solid #cfcfcf;border-top:2px solid var(--green);border-radius:3px;display:flex;align-items:center;justify-content:center}
.service h3{font-size:12px;font-weight:500;color:#222;margin-bottom:3px;margin-top:-2px}
.service p{font-size:8.6px;line-height:12px;color:#333}
.srule{height:1px;background:var(--line)}
.testimonial{left:89px;top:848px;width:625px;height:105px;background:#e9e9e9}
.avatar{left:106px;top:867px;width:56px;height:56px;border-radius:50%;background:linear-gradient(#c8ced8,#8a96a8);border:2px solid #fff;box-shadow:0 0 3px rgba(0,0,0,.3)}
.quote{left:190px;top:871px;width:497px;font-size:9px;line-height:14.5px;font-style:italic;color:#333}
.quote-rule{left:190px;top:920px;width:497px;height:1px;background:#ccc}
.author{left:192px;top:927px;font-size:9px;font-weight:700;color:#1a5ba8}
.dots{left:648px;top:934px;display:flex;gap:4px}
.dots i{width:6px;height:6px;border-radius:50%;background:#ccc}
.dots i:first-child{background:var(--green)}
.footer{left:0;top:953px;width:800px;height:217px;background:linear-gradient(var(--footer),#121212)}
.newsletter{left:95px;top:967px;width:611px;height:40px;background:#0e0e0e;border-radius:3px}
.newsletter h2{position:absolute;left:13px;top:8px;font-family:"Open Sans",sans-serif;font-weight:400;font-size:18px;color:#fff}
.newsletter p{position:absolute;left:177px;top:8px;width:150px;font-size:9px;line-height:12.5px;color:#ddd;border-left:1px solid #333;padding-left:12px}
.email{position:absolute;left:332px;top:11px;width:188px;height:19px;background:#fff;border-radius:2px;font-size:8px;color:#777;padding:5px}
.subscribe{position:absolute;left:524px;top:11px;width:76px;height:19px;background:linear-gradient(#7fd044,var(--green-dark));color:#fff;font-size:10.5px;font-weight:700;text-align:center;line-height:19px}
.ftitle{font-family:"Open Sans",sans-serif;font-size:12px;font-weight:600;color:#fff}
.frule{height:1px;background:#333}
.flink{font-size:8.5px;color:#ddd}
.flink::before{content:"›";color:#777;margin-right:8px}
.contact-row{display:flex;gap:10px;font-size:8.5px;line-height:12px;color:#ddd}
.flogo{left:546px;top:1058px;text-align:center;width:150px}
.flogo b{display:block;margin:0 auto 8px;width:34px;height:34px;border-radius:50%;background:#fff}
.flogo span{font-family:"Roboto",sans-serif;font-weight:700;font-size:17px;color:#fff}
.bottombar{left:0;top:1170px;width:800px;height:30px;background:var(--footer-deep)}
.copy{left:102px;top:11px;font-size:7.5px;color:#ccc}
.copy b{color:#fff}
.follow{left:554px;top:5px;display:flex;align-items:center;gap:5px;font-size:10px;color:#fff}
.follow i{width:19px;height:19px;border-radius:50%;background:#fff}
.follow i:first-of-type{background:var(--green)}
</style>
</head>
<body>
<div class="abs topstrip"></div>
<header class="abs header">
  <div class="abs brand" style="top:11px"><span class="brand-dot"></span><span class="brand-name">BRIVANE MANAGEMENT</span></div>
  <div class="abs help" style="top:18px">
    <span class="help-icon"><svg width="13" height="13" viewBox="0 0 24 24"><path fill="#fff" d="M6.6 10.8a15.1 15.1 0 0 0 6.6 6.6l2.2-2.2c.3-.3.7-.4 1-.2 1.1.4 2.3.6 3.6.6.6 0 1 .4 1 1V20c0 .6-.4 1-1 1A17 17 0 0 1 3 4c0-.6.4-1 1-1h3.5c.6 0 1 .4 1 1 0 1.3.2 2.5.6 3.6.1.3 0 .7-.2 1z"/></svg></span>
    <div><small>HAPPY TO HELP?</small><strong>012-555-0147</strong></div>
  </div>
</header>
<nav class="abs nav">
  <a class="active" style="left:90px;width:67px">HOME</a>
  <a style="left:157px;width:82px">ABOUT</a>
  <a style="left:239px;width:88px">SERVICES</a>
  <a style="left:327px;width:100px">RESOURCES</a>
  <a style="left:427px;width:92px;border-right:none">CONTACT</a>
  <div class="abs search"><span>search...</span><i><svg width="10" height="10" viewBox="0 0 10 10"><circle cx="4" cy="4" r="3" fill="none" stroke="#fff" stroke-width="1.4"/><path d="M6.3 6.3L9 9" stroke="#fff" stroke-width="1.6"/></svg></i></div>
</nav>
<section class="abs hero" role="img" aria-label="Photo of a businessman in a suit touching a screen with the words services, advice, help, customer"></section>
<div class="abs hero-copy"><h1>We Provides Management Consulting to theTravel Industry</h1><p>Lorem diam nonummy nibh esmod tincidu uta oreet dolore magna quam eratlutpat nim ad minim veniam quis nostrud nim adminim veniam.</p></div>
<div class="abs learn">LEARN MORE</div>
<div class="abs arrow" style="left:54px;top:200px"><svg width="8" height="10"><path d="M6 1L2 5l4 4" fill="none" stroke="#fff" stroke-width="1.5"/></svg></div>
<div class="abs arrow" style="left:722px;top:200px"><svg width="8" height="10"><path d="M2 1l4 4-4 4" fill="none" stroke="#fff" stroke-width="1.5"/></svg></div>

<main class="abs panel"></main>
<article class="abs box" style="left:100px">
  <div class="box-head"><b></b>ABOUT <em>BRIVANE</em></div>
  <div class="box-body">Lorem diam nonummy nibh esmod tincidu uta oreet dolore magna quam eratlutpat.nim ad minim veniam, quis nostrud nim adminim veniam, quis nostrud tationau ulamcorper scipit lortis nisl utnim ad minima veniarwem, quis nostrud exercin ulamco suscipit lobortis nisl utnim nim veniam, quis nostrud exerci scipit lortis nisl utnim ad minima veniarwem, nisl utnim nim veniam, quis nostrud exerci tation ulamcorper suscipit</div>
  <span class="plus"></span>
</article>
<article class="abs box" style="left:307px">
  <div class="box-head"><b></b>LATEST <em>NEWS</em></div>
  <div class="box-body">
    <div class="news" style="border-bottom:1px dotted #bbb;padding-bottom:8px"><div class="date"><span>09</span><span>OCT</span></div><div><h3>Lorem ipsum dolor sit amet</h3>is nisl utnim ad minima venam, quis nostrud exercin ulamcocipit lobortis nisl utnim nim veniam,is nisl utnimi ad minima veniam, quis</div></div>
    <div class="news"><div class="date"><span>09</span><span>OCT</span></div><div><h3>Lorem ipsum dolor sit amet</h3>Lorem ipsum smet consectetur mini adipisic elitsed do eit eim adosi miie vnioremipsuma</div></div>
  </div>
  <span class="plus"></span>
</article>
<article class="abs box" style="left:514px">
  <div class="box-head"><b></b>QUICK <em>CONTACT</em></div>
  <div style="padding-top:8px">
    <div class="field">Name</div><div class="field">Email</div><div class="field" style="height:52px">Message</div>
  </div>
  <span class="plus"></span>
</article>

<div class="abs tabline"></div>
<div class="abs tab">OUR <em>SERVICES</em></div>

<div class="abs srule" style="left:100px;top:622px;width:280px"></div>
<div class="abs srule" style="left:417px;top:622px;width:280px"></div>
<div class="abs service" style="left:110px;top:623px"><div class="service-icon"><svg width="34" height="32" viewBox="0 0 34 32"><rect x="3" y="20" width="4" height="10" fill="#222"/><rect x="10" y="16" width="4" height="14" fill="#222"/><rect x="17" y="12" width="4" height="18" fill="#222"/><rect x="24" y="8" width="4" height="22" fill="#222"/><path d="M3 15L24 3" stroke="#1a6fc4" stroke-width="2.5"/><path d="M20 2h6v6z" fill="#1a6fc4"/></svg></div><div><h3 style="margin-top:4px">Sales/ Marketing</h3><p>Lorem ipsum dolor sit amet consectetur elitsed do eiusmod tempor incididunt ut labore et dolore magna aliqua ut enim ad minim vesniam.</p></div></div>
<div class="abs service" style="left:427px;top:623px"><div class="service-icon"><svg width="34" height="32" viewBox="0 0 34 32"><circle cx="13" cy="8" r="6" fill="#222"/><path d="M2 30c0-10 5-14 11-14s11 4 11 14z" fill="#222"/><circle cx="25" cy="23" r="7" fill="#fff" stroke="#1a6fc4" stroke-width="2"/><path d="M25 19v4h3" stroke="#1a6fc4" stroke-width="1.6" fill="none"/></svg></div><div><h3 style="margin-top:4px">Strategic Planning</h3><p>Lorem ipsum dolor sit amet consectetur elitsed do eiusmod tempor incididunt ut labore et dolore magna aliqua ut enim ad minim vesniam.</p></div></div>

<div class="abs srule" style="left:100px;top:695px;width:280px"></div>
<div class="abs srule" style="left:417px;top:695px;width:280px"></div>
<div class="abs service" style="left:110px;top:695px"><div class="service-icon"><svg width="34" height="32" viewBox="0 0 34 32"><circle cx="12" cy="5" r="4" fill="#222"/><rect x="8" y="10" width="8" height="14" rx="2" fill="#222"/><circle cx="23" cy="20" r="8" fill="#1a6fc4"/><text x="23" y="24" font-size="11" font-family="Roboto,sans-serif" font-weight="700" fill="#fff" text-anchor="middle">$</text></svg></div><div><h3>Human Capital Management Solutions</h3><p>Lorem ipsum dolor sit amet consectetsed do eiusmod tempor incididunt ut labore et dolore magna aliqua ut enim ad minim vesniam.</p></div></div>
<div class="abs service" style="left:427px;top:695px"><div class="service-icon"><svg width="36" height="32" viewBox="0 0 36 32"><rect x="2" y="3" width="26" height="20" fill="none" stroke="#222" stroke-width="2.5"/><path d="M6 17l6-7 5 5 7-8" stroke="#222" stroke-width="2" fill="none"/><circle cx="26" cy="21" r="5" fill="#fff" stroke="#1a6fc4" stroke-width="2.5"/><path d="M30 25l4 4" stroke="#1a6fc4" stroke-width="3"/></svg></div><div><h3>Financial Analysis</h3><p>Lorem ipsum dolor sit amet consectetur elitsed do eiusmod tempor incididunt ut labore et dolore magna aliqua ut enim ad minim vesniam.</p></div></div>

<div class="abs srule" style="left:100px;top:773px;width:280px"></div>
<div class="abs srule" style="left:417px;top:773px;width:280px"></div>
<div class="abs service" style="left:110px;top:774px"><div class="service-icon"><svg width="34" height="32" viewBox="0 0 34 32"><rect x="2" y="8" width="26" height="18" rx="2" fill="#222"/><rect x="11" y="4" width="8" height="5" fill="none" stroke="#222" stroke-width="2"/><rect x="2" y="15" width="26" height="2" fill="#666"/><circle cx="27" cy="24" r="5" fill="#1a6fc4"/><text x="27" y="27" font-size="8" font-family="Roboto,sans-serif" font-weight="700" fill="#fff" text-anchor="middle">$</text></svg></div><div><h3>Cash Management Solutions</h3><p>Lorem ipsum dolor sit amet consectetur elitsed do eiusmod tempor incididunt ut labore et dolore magna aliqua ut enim ad minim vesniam.</p></div></div>
<div class="abs service" style="left:427px;top:774px"><div class="service-icon"><svg width="34" height="32" viewBox="0 0 34 32"><path d="M6 18a11 11 0 0 1 22 0" fill="none" stroke="#222" stroke-width="3"/><rect x="4" y="16" width="6" height="10" rx="2" fill="#222"/><rect x="24" y="16" width="6" height="10" rx="2" fill="#222"/><path d="M27 26c0 3-4 4-8 4" fill="none" stroke="#1a6fc4" stroke-width="2"/></svg></div><div><h3>Customer Support</h3><p>Lorem ipsum dolor sit amet consectetur elitsed do eiusmod tempor incididunt ut labore et dolore magna aliqua ut enim ad minim vesniam.</p></div></div>

<section class="abs testimonial"></section>
<div class="abs avatar" role="img" aria-label="Portrait photo of the client quoted"></div>
<span class="abs" style="left:178px;top:858px;font-size:28px;color:#bbb;font-family:Georgia,serif">&ldquo;</span>
<p class="abs quote">Lorem ipsum dolor sit amet consectetur adipisicing elitsed do eiusmod tempor incididunt ut labore et dolore magna aliqua. Ut enim ad minim vesniam, quis nostrud exercitation ullamco laboris nisi ut aliquip ex ea commodo consequat. Duis aute irure dolor in reprehenderit in voluptate velit esse cillum is a dolore eu fugiat nulla pariatur. Excepteur sint occaecat cupidatat non proi</p>
<span class="abs" style="left:648px;top:893px;font-size:28px;color:#bbb;font-family:Georgia,serif">&rdquo;</span>
<div class="abs quote-rule"></div>
<div class="abs author">Daniel Hart</div>
<div class="abs dots"><i></i><i></i><i></i><i></i></div>

<footer class="abs footer"></footer>
<div class="abs newsletter"><h2>Newsletter Signup</h2><p>Get latest updates by entering your email address.</p><div class="email">Enter your Email...</div><div class="subscribe">SUBSCRIBE</div></div>

<div class="abs ftitle" style="left:102px;top:1041px">QUICK LINKS</div>
<div class="abs frule" style="left:102px;top:1062px;width:186px"></div>
<div class="abs flink" style="left:106px;top:1072px">Home</div>
<div class="abs flink" style="left:106px;top:1101px">Services</div>
<div class="abs flink" style="left:106px;top:1131px">Contact Us</div>
<div class="abs flink" style="left:206px;top:1075px">About Us</div>
<div class="abs flink" style="left:206px;top:1101px">Resources</div>
<div class="abs frule" style="left:102px;top:1092px;width:80px"></div>
<div class="abs frule" style="left:102px;top:1121px;width:80px"></div>
<div class="abs frule" style="left:102px;top:1150px;width:80px"></div>
<div class="abs frule" style="left:204px;top:1093px;width:84px"></div>
<div class="abs frule" style="left:204px;top:1121px;width:84px"></div>

<div class="abs ftitle" style="left:320px;top:1041px">CONTACT US</div>
<div class="abs frule" style="left:320px;top:1062px;width:188px"></div>
<div class="abs contact-row" style="left:320px;top:1074px;width:190px"><svg width="9" height="12" viewBox="0 0 9 12" style="flex:none"><path d="M4.5 0A4.5 4.5 0 0 0 0 4.5C0 8 4.5 12 4.5 12S9 8 9 4.5A4.5 4.5 0 0 0 4.5 0z" fill="#fff"/><circle cx="4.5" cy="4.5" r="1.6" fill="#1c1c1c"/></svg><span>Lorem ipsum dolor sit amet consecttuer adi piscing elit diam non</span></div>
<div class="abs contact-row" style="left:320px;top:1106px"><svg width="9" height="10" viewBox="0 0 24 24" style="flex:none"><path fill="#fff" d="M6.6 10.8a15.1 15.1 0 0 0 6.6 6.6l2.2-2.2c.3-.3.7-.4 1-.2 1.1.4 2.3.6 3.6.6.6 0 1 .4 1 1V20c0 .6-.4 1-1 1A17 17 0 0 1 3 4c0-.6.4-1 1-1h3.5c.6 0 1 .4 1 1 0 1.3.2 2.5.6 3.6.1.3 0 .7-.2 1z"/></svg><span>012-555-0147</span></div>
<div class="abs contact-row" style="left:320px;top:1127px"><svg width="10" height="8" viewBox="0 0 10 8" style="flex:none"><rect width="10" height="8" fill="#fff"/><path d="M0 0l5 4 5-4" fill="none" stroke="#1c1c1c"/></svg><span>www.info@brivanemgmt.com</span></div>
<div class="abs" style="left:524px;top:1020px;width:1px;height:148px;background:#2c2c2c"></div>
<div class="abs flogo"><b></b><span>BRIVANE MANAGEMENT</span></div>

<div class="abs bottombar">
  <div class="abs copy">Copyright 2014 <b>brivanemanagement.</b> All Right Reserved.</div>
  <div class="abs follow">FOLLOW US :<i></i><i></i><i></i><i></i></div>
</div>
</body>
</html>
```